Brenwick Structures Construction Company Seeking Modern Website

We are a small construction company wanting to create a web presence. We don't have much in the way of current content but will get photos as they come in. Attached is a picture of our business card.
The pages we would like on the menu are:
Home
Portfolio
Product Specs
Testimonials
Our Process
Contact
Some designs we like are:
http://www.tovasheds-example.com/
http://www.qrnstructures-example.com/
http://dunholtbarns-example.com/
http://pellingframes-example.com/
Not much requirements other than that so feel free to be creative!
Updates
Target Market(s)
Construction
Commercial and Residential Buildings
Industry/Entity Type
Construction Company
Number of Pages Required
5+ page
Look and feel

```html
<!DOCTYPE html>
<html lang="en">
<head>
<meta charset="utf-8">
<title>Brenwick Structures</title>
<link href="https://fonts.googleapis.com/css2?family=Roboto:wght@300;400;500;700&family=Roboto+Condensed:wght@400;700&display=swap" rel="stylesheet">
<style>
:root{
  --sky:#d9f2fc;
  --blue:#1aa6dd;
  --ink:#222;
  --dark:#3a3a3a;
  --footer:#2b2b2b;
  --muted:#6b6b6b;
  --white:#fff;
}
*{margin:0;padding:0;box-sizing:border-box}
html,body{width:674px;height:1200px;overflow:hidden;background:var(--white);font-family:"Roboto",sans-serif;color:var(--ink)}
.page{position:relative;width:674px;height:1200px}
.abs{position:absolute}

.site-header{left:0;top:0;width:674px;height:77px;background:var(--sky)}
.main-nav{right:62px;top:30px;display:flex;align-items:center;gap:0;font-family:"Roboto Condensed",sans-serif;font-size:7px}
.main-nav a{color:var(--ink);text-decoration:none;padding:4px 9px;border-radius:10px}
.main-nav a.active{background:var(--blue);color:var(--white);padding:4px 11px}
.search-icon{right:48px;top:34px}

.brand-tab{left:55px;top:54px;width:190px;height:52px;background:var(--white);border-radius:0 0 95px 95px / 0 0 40px 40px;z-index:3;display:flex;align-items:center;justify-content:center}
.brand-name{font-family:"Roboto",sans-serif;font-weight:700;font-size:16px;color:var(--blue);margin-top:-12px}

.hero{left:0;top:77px;width:674px;height:344px;background:linear-gradient(180deg,#5d9fc7 0%,#9cc8de 45%,#c79a55 75%,#8a6a3c 100%)}
.hero-caption{left:55px;top:136px;width:320px;height:75px;background:rgba(70,70,70,.75);border-left:7px solid var(--blue);padding:14px 0 0 20px;color:var(--white)}
.hero-caption h1{font-size:20px;font-weight:500;letter-spacing:.2px}
.hero-caption p{font-size:10px;font-weight:300;margin-top:8px}
.hero-arrow{top:155px}

.welcome{left:0;top:421px;width:674px;height:191px;background:var(--dark);text-align:center;color:var(--white)}
.welcome h2{margin-top:33px;font-size:15px;font-weight:500}
.welcome .tag{margin-top:10px;font-size:6px;color:var(--blue)}
.welcome .intro{margin:14px auto 0;width:480px;font-size:6.4px;line-height:12.5px;color:#e6e6e6}
.btn{display:inline-block;margin-top:14px;width:84px;height:24px;line-height:24px;border-radius:50%;background:var(--blue);color:var(--white);font-size:6.5px;font-weight:500;text-decoration:none}

.service-card{top:645px;width:273px;height:143px;box-shadow:0 0 3px rgba(0,0,0,.25)}
.service-card .shade{left:77px;top:0;width:120px;height:143px;background:rgba(70,70,70,.55)}
.service-card .label{left:0;top:0;width:273px;height:143px;display:flex;align-items:center;justify-content:center;text-align:center;color:var(--white);font-size:12px;font-weight:500;line-height:14.5px}
.card-residential{left:55px;background:linear-gradient(135deg,#2e5d86,#8fb6d4 55%,#dfeaf3)}
.card-commercial{left:346px;background:linear-gradient(160deg,#5a8fc2,#c8d9ea 50%,#b1a25a)}

.section-title{left:0;top:817px;width:674px;text-align:center;font-size:14px;font-weight:700;color:var(--blue)}

.post{top:853px;width:134px}
.post .thumb{width:134px;height:97px;box-shadow:0 0 3px rgba(0,0,0,.2)}
.post h3{margin-top:15px;font-size:8px;font-weight:500;color:var(--blue)}
.post p{margin-top:3px;font-size:6.4px;line-height:12.5px;color:var(--muted)}
.post .more{display:flex;align-items:center;gap:4px;margin-top:5px;font-family:"Roboto Condensed",sans-serif;font-size:6px;color:var(--blue)}

.site-footer{left:0;top:1080px;width:674px;height:120px;background:var(--footer);border-top:3px solid var(--blue);border-bottom:3px solid var(--blue);color:var(--white)}
.footer-brand{left:56px;top:28px;font-size:18px;font-weight:700;color:var(--blue)}
.footer-info{left:56px;top:68px;font-size:6.4px;line-height:16px}
.footer-nav{right:56px;top:39px;font-size:6.5px;display:flex;gap:7px}
.footer-nav span.sep{opacity:.8}
.social{right:56px;top:63px;display:flex;align-items:center;gap:6px;font-size:6.4px}
.social i{display:block;width:16px;height:16px;border-radius:50%;background:#6b6b6b}
</style>
</head>
<body>
<div class="page">

  <header class="site-header abs">
    <nav class="main-nav abs">
      <a class="active" href="#">Home</a>
      <a href="#">Portfolio</a>
      <a href="#">Product Specs</a>
      <a href="#">Testimonials</a>
      <a href="#">Our Process</a>
      <a href="#">Contact</a>
    </nav>
    <svg class="search-icon abs" width="9" height="9" viewBox="0 0 9 9"><circle cx="3.6" cy="3.6" r="2.7" fill="none" stroke="#222" stroke-width="1.3"/><line x1="5.6" y1="5.6" x2="8.3" y2="8.3" stroke="#222" stroke-width="1.4"/></svg>
  </header>

  <div class="brand-tab abs"><span class="brand-name">Brenwick Structures</span></div>

  <section class="hero abs" role="img" aria-label="Construction site with tower crane and steel frames under a blue sky">
    <svg class="hero-arrow abs" style="left:9px" width="36" height="36" viewBox="0 0 36 36"><circle cx="18" cy="18" r="16" fill="none" stroke="rgba(255,255,255,.5)" stroke-width="2"/><polyline points="21,11 14,18 21,25" fill="none" stroke="rgba(255,255,255,.6)" stroke-width="2"/></svg>
    <svg class="hero-arrow abs" style="right:9px" width="36" height="36" viewBox="0 0 36 36"><circle cx="18" cy="18" r="16" fill="none" stroke="rgba(255,255,255,.5)" stroke-width="2"/><polyline points="15,11 22,18 15,25" fill="none" stroke="rgba(255,255,255,.6)" stroke-width="2"/></svg>
  </section>
  <div class="hero-caption abs">
    <h1>OUR TARGETS</h1>
    <p>Commercial Construction and Residential Buildings</p>
  </div>

  <section class="welcome abs">
    <h2>WELCOME TO BRENWICK STRUCTURES</h2>
    <p class="tag">Small construction company</p>
    <p class="intro">Lorem Ipsum is simply dummy text of the printing and typesetting industry. Lorem Ipsum has been the industry's standard dummy text ever since the 1500s, when an unknown printer took a galley of type and scrambled it to make a type specimen book. It has survived not only five centuries, but also the leap into electronic typesetting, remaining essentially unchanged. It was popularised in the 1960s...</p>
    <a class="btn" href="#">READ MORE</a>
  </section>

  <div class="service-card card-residential abs" role="img" aria-label="Glass residential towers seen from below">
    <div class="shade abs"></div>
    <div class="label abs">RESIDENTIAL<br>BUILDINGS</div>
  </div>
  <div class="service-card card-commercial abs" role="img" aria-label="Cranes over a commercial building site with a worker in a hard hat">
    <div class="shade abs"></div>
    <div class="label abs">COMMERCIAL<br>CONSTRUCTION</div>
  </div>

  <h2 class="section-title abs">BLOG POSTS</h2>

  <article class="post abs" style="left:56px">
    <div class="thumb" role="img" aria-label="House front porch with garden" style="background:linear-gradient(180deg,#6f9fd6,#7c8a9a 45%,#6f7d55)"></div>
    <h3>RESIDENTIAL BUILDINGS</h3>
    <p>Em investimentos alternativos, além de recursos financeiros, a K:7 traz para a mesa sua vasta experiência adquirida em diversos ciclos de mercado,</p>
    <div class="more">READ MORE <svg width="6" height="6" viewBox="0 0 6 6"><circle cx="3" cy="3" r="3" fill="#1aa6dd"/><polyline points="2.3,1.6 3.7,3 2.3,4.4" fill="none" stroke="#fff" stroke-width=".9"/></svg></div>
  </article>
  <article class="post abs" style="left:199px">
    <div class="thumb" role="img" aria-label="Modern single storey home with lawn" style="background:linear-gradient(180deg,#9aa3ab,#e2e2e2 45%,#7d8f5a 70%,#4f6b30)"></div>
    <h3>RESIDENTIAL BUILDINGS</h3>
    <p>Em investimentos alternativos, além de recursos financeiros, a K:7 traz para a mesa sua vasta experiência adquirida em diversos ciclos de mercado,</p>
    <div class="more">READ MORE <svg width="6" height="6" viewBox="0 0 6 6"><circle cx="3" cy="3" r="3" fill="#1aa6dd"/><polyline points="2.3,1.6 3.7,3 2.3,4.4" fill="none" stroke="#fff" stroke-width=".9"/></svg></div>
  </article>
  <article class="post abs" style="left:342px">
    <div class="thumb" role="img" aria-label="Multi storey concrete frame under construction" style="background:linear-gradient(180deg,#5f9bd8,#cfdbe6 40%,#9a6a55 70%,#8a8a8a)"></div>
    <h3>COMMERCIAL CONSTRUCTIONS</h3>
    <p>Em investimentos alternativos, além de recursos financeiros, a K:7 traz para a mesa sua vasta experiência adquirida em diversos ciclos de mercado,</p>
    <div class="more">READ MORE <svg width="6" height="6" viewBox="0 0 6 6"><circle cx="3" cy="3" r="3" fill="#1aa6dd"/><polyline points="2.3,1.6 3.7,3 2.3,4.4" fill="none" stroke="#fff" stroke-width=".9"/></svg></div>
  </article>
  <article class="post abs" style="left:484px">
    <div class="thumb" role="img" aria-label="Tower cranes above a building site" style="background:linear-gradient(180deg,#4d8fd6,#a9c9e6 45%,#c9a24a 75%,#9c9c9c)"></div>
    <h3>COMMERCIAL CONSTRUCTIONS</h3>
    <p>Em investimentos alternativos, além de recursos financeiros, a K:7 traz para a mesa sua vasta experiência adquirida em diversos ciclos de mercado,</p>
    <div class="more">READ MORE <svg width="6" height="6" viewBox="0 0 6 6"><circle cx="3" cy="3" r="3" fill="#1aa6dd"/><polyline points="2.3,1.6 3.7,3 2.3,4.4" fill="none" stroke="#fff" stroke-width=".9"/></svg></div>
  </article>

  <footer class="site-footer abs">
    <div class="footer-brand abs">Brenwick Structures</div>
    <div class="footer-info abs">PO Box 412 Harlow Lane, Greyfield-30518 .<br>Copyright @ 2015 . Brenwick Structures &nbsp;| All Rights Reserved.</div>
    <nav class="footer-nav abs">
      <span>Home</span><span class="sep">/</span><span>Portfolio</span><span class="sep">/</span><span>Product Specs</span><span class="sep">/</span><span>Testimonials</span><span class="sep">/</span><span>Our Process</span><span class="sep">/</span><span>Contact</span>
    </nav>
    <div class="social abs"><span>Stay Connected :</span><i></i><i></i><i></i><i></i></div>
  </footer>

</div>
</body>
</html>
```